ULMIRA card Technical Architecture

Hello everyone ULMIRA: It is a consulting firm in Architecture and Construction. I require a card duplexing, sober, elegant, classic but not boring. Update 1: Use the following data for the card. Name: Gonzalo Pereda Mauricio Villalta Position: COO Twitter: @ulmiraAT Homepage: ulmira-example.com home address not include the participation of all thank you.

Target Market(s)

Construction companies, Architects and Consulting Engineers

Industry/Entity Type

Consulting

Contact Information for Business Card

Los campos que debe tener:
Nombre, Cargo, email, homepage y twitter

Font styles to use
Serif
Sans Serif
Other font styles liked:
• Me gustan playfair display, open sans y roboto, pero estoy sujeto a sus propuestas

Requirements
Must have
• Colors: Present combined proposals in white, red, gray and black Update 1: The two names must be clearly differentiated from the two surnames
Nice to have
• They are free to present their best proposals. I will bring them immediate feedback to the extent you can go see their designs. Complete data for card and logo files will give the winner the

```html
<!DOCTYPE html>
<html lang="es">
<head>
<meta charset="utf-8">
<title>ULMIRA – Business Card</title>
<link href="https://fonts.googleapis.com/css2?family=Roboto:wght@300;400;500&display=swap" rel="stylesheet">
<style>
  :root {
    --page-bg: #8a8a8a;
    --card-bg: #050607;
    --red: #d0262f;
    --red-soft: #c42a36;
    --white: #ffffff;
    --light: #e8e8e8;
  }
  * { margin: 0; padding: 0; box-sizing: border-box; }
  html, body {
    width: 1200px; height: 1200px; overflow: hidden;
    background: var(--page-bg);
    font-family: "Roboto", Arial, sans-serif;
  }
  .card {
    position: absolute; left: 238px; width: 686px; height: 388px;
    background: var(--card-bg); border-radius: 16px; overflow: hidden;
  }
  .card--front { top: 182px; }
  .card--back  { top: 631px; }

  /* front */
  .brand {
    position: absolute; left: 0; right: 0; top: 150px;
    display: flex; justify-content: center; align-items: center; gap: 14px;
  }
  .brand__square { width: 26px; height: 26px; background: var(--red); }
  .brand__name {
    color: var(--white); font-weight: 400; font-size: 40px; letter-spacing: 12px;
  }
  .front__url {
    position: absolute; left: 0; right: 0; top: 348px; text-align: center;
    color: var(--light); font-weight: 300; font-size: 18px;
  }

  /* back */
  .lockup { position: absolute; left: 374px; width: 290px; top: 70px; }
  .lockup__square { width: 22px; height: 22px; background: var(--red); margin: 0 auto 12px; }
  .lockup__name {
    color: var(--white); font-weight: 400; font-size: 40px; letter-spacing: 15px;
    text-align: center; line-height: 46px; padding-left: 15px;
  }
  .lockup__rule { height: 1px; background: var(--red); margin-top: 4px; }
  .lockup__tagline {
    color: var(--red); font-size: 12px; letter-spacing: 5.2px; text-align: center;
    margin-top: 6px; white-space: nowrap;
  }

  .person { position: absolute; left: 0; top: 296px; padding-left: 28px; }
  .person__bar {
    position: absolute; left: 0; top: 0; width: 13px; height: 50px; background: var(--red);
  }
  .person__name { color: var(--white); font-weight: 500; font-size: 27px; line-height: 30px; }
  .person__role { color: var(--red-soft); font-weight: 300; font-size: 19px; line-height: 24px; }

  .contacts { position: absolute; left: 304px; top: 290px; list-style: none; }
  .contacts li {
    display: flex; align-items: center; gap: 7px; height: 23px;
    color: var(--light); font-weight: 300; font-size: 19px;
  }
  .contacts svg { width: 13px; height: 13px; flex: none; }
</style>
</head>
<body>

<section class="card card--front">
  <div class="brand">
    <span class="brand__square"></span>
    <span class="brand__name">ULMIRA</span>
  </div>
  <p class="front__url">www.ulmira-example.com</p>
</section>

<section class="card card--back">
  <div class="lockup">
    <div class="lockup__square"></div>
    <div class="lockup__name">ULMIRA</div>
    <div class="lockup__rule"></div>
    <div class="lockup__tagline">ARQUITECTURA TÉCNICA</div>
  </div>

  <div class="person">
    <span class="person__bar"></span>
    <p class="person__name">Gonzalo Pereda</p>
    <p class="person__role">Managing Partner</p>
  </div>

  <ul class="contacts">
    <li>
      <svg viewBox="0 0 14 14" aria-hidden="true"><rect x="0.5" y="2.5" width="13" height="9" fill="#d0262f"/><path d="M0.5 2.5 L7 8 L13.5 2.5" fill="none" stroke="#050607" stroke-width="1"/></svg>
      gpereda@ulmira-example.com
    </li>
    <li>
      <svg viewBox="0 0 14 14" aria-hidden="true" fill="none" stroke="#d0262f" stroke-width="1.1"><circle cx="7" cy="7" r="6"/><ellipse cx="7" cy="7" rx="2.6" ry="6"/><path d="M1 7h12M2 4h10M2 10h10"/></svg>
      www.ulmira-example.com
    </li>
    <li>
      <svg viewBox="0 0 14 14" aria-hidden="true"><rect x="1" y="1" width="12" height="12" fill="#d0262f"/></svg>
      @ULMIRA
    </li>
  </ul>
</section>

</body>
</html>
```